Bright and beautiful business card for a coach

I'm a personal and business coach based in Perth, Australia. I need a business card that whilst subtle and elegant, will stand out and appeal on a table full of cards.

My business name is Fern Mentoring and the business card must represent the warmth and brightness implied in the name, without being gimmicky. It must have a warmth and appeal and be easy to read.

I prefer clean, minimalist designs.

It must align with the feel of my website and socials: https://www.fernmentoring-example.com.au/
https://www.instagram.com/fernmentoringau/
https://www.facebook.com/fernmentoringau
Updates

Hi Designers Thank you so much for taking the time to submit designs. I wonder if I could have explained myself a little better. Most of the designs that have been submitted look rather formal and many have quite corporate looking embellishments on them (to my eye). I would like softer, warmer, more organic. I’m open to people playing about and being more abstract, using softer embellishments (e.g the line drawing flowers and grasses I’ve used in my socials) incorporating other colours from my palette or like the social icons in my email signature (in PDF), perhaps playing with size/oversize, playing with the bleed. Please don’t be constrained by what I’ve already done, it merely needs to compliment. I’m sorry if I’m not using the right words or have led you astray. I’m no designer, but I’ve done my website, socials, email signature etc all myself (my logo was a design contest) and I was really hoping for my business card to be something more creative than I could have made with a template. Reminder: No black cards/sides please. Thank you 😊

Target Market(s)

Individuals, most likely but not all female. Creative thinkers. Likely professionals.

Industry/Entity Type

Business & Personal Coach

Contact Information for Business Card

(Fern Mentoring Logo) Name: Greta Pellham; Title: Business & Personal Coach; Phone number: +61 (0)458 913307; Email: greta@fernmentoring-example.com.au; Website: https://fernmentoring-example.com.au; Social icons for Facebook, Instagram & LinkedIn: @fernmentoringAU. Optional strapline: "A thinking partner to help you cut through the noise"

Font styles to use
Sans Serif

Colors
00AB8E
00BBA5
67D7C9
C6EFE9
E9F9F6
59FF00
82FF00
B8FF75
E3FFCB
F4FFEA
FFC000
F8CF3A
FAE287
FDF2CF
FEFAEE

Requirements
Must have
• Must align with feel of my website and socials. Must have a pop of #FFC000 (possibly whole of one side, or at least a block). Bright or white background. Easy to read.
Nice to have
• Possibly incorporate the sunshine/grass picture I have used in website and socials - will upload.
Should not have
• Must not be black or dark. Not impersonal or corporate looking.

```html
<!DOCTYPE html>
<html lang="en">
<head>
<meta charset="utf-8">
<title>Fern Mentoring – Business Card</title>
<link rel="stylesheet" href="https://fonts.googleapis.com/css2?family=Work+Sans:wght@400;500&family=Pinyon+Script&display=swap">
<style>
  :root {
    --backdrop: #efe7d8;
    --card-yellow: #f2b51d;
    --sun-yellow: #f8c62b;
    --copper: #c98535;
    --copper-deep: #a9621f;
    --slate: #6f7a79;
    --slate-deep: #55605f;
    --white: #ffffff;
  }
  * { margin: 0; padding: 0; box-sizing: border-box; }
  html, body {
    width: 1200px; height: 800px; overflow: hidden;
    background: var(--backdrop);
  }
  .sheet {
    width: 1200px; height: 800px;
    display: flex; align-items: center; justify-content: center; gap: 48px;
  }
  .card {
    width: 520px; height: 297px; display: block;
    box-shadow: 0 14px 30px rgba(120, 80, 20, .22);
  }
  .brand-name {
    font-family: "Work Sans", sans-serif; font-weight: 500;
    font-size: 25px; letter-spacing: .22em; fill: var(--white);
  }
  .person-name {
    font-family: "Pinyon Script", cursive; font-size: 34px; fill: var(--white);
  }
  .person-title {
    font-family: "Work Sans", sans-serif; font-weight: 400;
    font-size: 11.5px; letter-spacing: .04em; fill: var(--white);
  }
  .contact-line {
    font-family: "Work Sans", sans-serif; font-weight: 400;
    font-size: 11px; letter-spacing: .02em; fill: var(--white);
  }
  .rule { stroke: var(--white); stroke-width: 1; }
  .social-dot { fill: var(--white); }
</style>
</head>
<body>
<main class="sheet">

  <!-- Front of card -->
  <svg class="card card-front" viewBox="0 0 520 297" role="img" aria-label="Fern Mentoring business card, front">
    <defs>
      <linearGradient id="copperFade" x1="0" y1="0" x2="1" y2="0">
        <stop offset="0" stop-color="var(--copper)"/>
        <stop offset="1" stop-color="var(--copper-deep)"/>
      </linearGradient>
      <linearGradient id="slateFade" x1="0" y1="0" x2="1" y2="1">
        <stop offset="0" stop-color="var(--slate)"/>
        <stop offset="1" stop-color="var(--slate-deep)"/>
      </linearGradient>
      <clipPath id="frontClip"><rect width="520" height="297"/></clipPath>
    </defs>
    <g clip-path="url(#frontClip)">
      <rect class="front-base" width="520" height="297" fill="url(#copperFade)"/>
      <circle class="front-slate-arc" cx="575" cy="150" r="130" fill="url(#slateFade)"/>
      <circle class="front-sun" cx="70" cy="148" r="275" fill="var(--sun-yellow)"/>
      <text class="brand-name" x="180" y="142" text-anchor="middle">FERN</text>
      <text class="brand-name" x="180" y="176" text-anchor="middle">MENTORING</text>
    </g>
  </svg>

  <!-- Back of card -->
  <svg class="card card-back" viewBox="0 0 520 297" role="img" aria-label="Fern Mentoring business card, back with contact details">
    <defs>
      <linearGradient id="slatePanel" x1="0" y1="0" x2="1" y2="1">
        <stop offset="0" stop-color="var(--slate)"/>
        <stop offset="1" stop-color="var(--slate-deep)"/>
      </linearGradient>
      <clipPath id="backClip"><rect width="520" height="297"/></clipPath>
    </defs>
    <g clip-path="url(#backClip)">
      <rect class="back-base" width="520" height="297" fill="var(--card-yellow)"/>
      <circle class="back-copper-dot" cx="175" cy="255" r="62" fill="var(--copper)"/>
      <path class="back-panel" d="M520 0 H300 A135 135 0 0 0 165 135 V297 H520 Z" fill="url(#slatePanel)"/>

      <text class="person-name" x="200" y="92">Greta Pellham</text>
      <text class="person-title" x="202" y="114">Business &amp; Personal Coach</text>
      <line class="rule" x1="202" y1="126" x2="478" y2="126"/>
      <text class="contact-line" x="202" y="154">greta@fernmentoring-example.com.au</text>
      <text class="contact-line" x="202" y="176">+61 (0)458 913307</text>
      <text class="contact-line" x="202" y="198">https://fernmentoring-example.com.au</text>
      <circle class="social-dot" cx="208" cy="221" r="6"/>
      <text class="contact-line" x="222" y="225">@fernmentoringAU</text>
    </g>
  </svg>

</main>
</body>
</html>
```